Post storm repair flyer

looking for an eye catching 6x9 postcard to send out to single family home owners advertising a "Post Storm Repair Special" explaining that after the recent hurricanes its very important to have your roof checked and any repairs fixed right away before they become a bigger more costly problem and that even though your home wasn't directly hit by the storm the high wind gust could've cause unseen damage.
offer $200 off any repair *some rules may apply
Crest Roofing
877.512.DUNE
www.DuneRoofingco.example

```html
<!DOCTYPE html>
<html lang="en">
<head>
<meta charset="utf-8">
<title>Crest Roofing – Post Storm Repair Special Postcard</title>
<link rel="stylesheet" href="https://fonts.googleapis.com/css2?family=Montserrat:wght@500;600;700;800&family=Nunito+Sans:wght@400;600&display=swap">
<style>
  :root{
    --backdrop:#7a7a7a;
    --ink:#2b2b2b;
    --charcoal:#2d2c2c;
    --gold:#e8b330;
    --white:#ffffff;
    --stamp:#d4d4d4;
    --rule:#555555;
    --sky-top:#4a8fd6;
    --sky-mid:#8fb7e0;
    --roof-tan:#c9a66b;
    --siding:#b7bcc4;
    --lawn:#5f8a3a;
  }
  *{box-sizing:border-box;margin:0;padding:0}
  html,body{width:1200px;height:2323px;overflow:hidden}
  body{background:var(--backdrop);font-family:"Nunito Sans",sans-serif;color:var(--ink);position:relative}

  .postcard{position:absolute;left:150px;width:900px;height:600px;overflow:hidden}
  .postcard--front{top:360px;background:var(--charcoal)}
  .postcard--back{top:1360px;background:var(--white)}

  /* front */
  .hero-photo{position:absolute;left:0;top:0;width:900px;height:438px;
    background:linear-gradient(180deg,var(--sky-top) 0%,var(--sky-mid) 38%,var(--roof-tan) 55%,var(--siding) 72%,var(--lawn) 100%)}
  .headline{position:absolute;left:55px;top:60px;font-family:"Montserrat",sans-serif;font-weight:600;line-height:1}
  .headline__top{display:inline-block;background:var(--charcoal);color:var(--white);font-size:56px;padding:8px 20px 8px 36px;clip-path:polygon(0 0,100% 0,100% 100%,6% 100%)}
  .headline__bottom{display:block;margin:-2px 0 0 70px;width:max-content;background:var(--gold);color:var(--charcoal);font-size:44px;padding:8px 24px 8px 10px;clip-path:polygon(0 0,100% 0,95% 100%,0 100%)}

  .brand{position:absolute;display:flex;align-items:center;gap:8px;font-family:"Montserrat",sans-serif;font-weight:600;color:var(--charcoal);font-size:17px;letter-spacing:.3px}
  .brand__mark{width:14px;height:14px;background:var(--charcoal)}
  .postcard--front .brand{right:32px;top:80px}

  .offer{position:absolute;left:42px;top:347px;width:300px;height:163px;background:var(--gold);border-radius:14px;color:var(--charcoal);font-family:"Montserrat",sans-serif}
  .offer__headline{position:absolute;left:28px;top:10px;display:flex;align-items:center;gap:4px}
  .offer__amount{font-size:84px;font-weight:800;letter-spacing:-3px;line-height:1.05}
  .offer__off{font-size:17px;font-weight:800;margin-top:-4px}
  .offer__what{position:absolute;left:66px;top:106px;font-size:27px;font-weight:700}
  .offer__terms{position:absolute;left:150px;top:140px;font-size:10px;color:var(--white);font-weight:500}

  .thumb{position:absolute;top:350px;width:236px;height:162px;border:4px solid var(--white);border-radius:14px}
  .thumb--shingles{left:365px;background:linear-gradient(160deg,#8a7c6e,#5b534d 60%,#9a8d7f)}
  .thumb--tiles{left:625px;background:linear-gradient(180deg,#e6e2dc 0%,#c8c2b8 30%,#b4563a 55%,#8e3c27 100%)}

  .front-contact{position:absolute;display:flex;align-items:center;gap:8px;color:var(--white);font-family:"Montserrat",sans-serif;font-weight:600;white-space:nowrap}
  .front-contact--phone{left:72px;top:525px;font-size:44px}
  .front-contact--web{right:45px;top:538px;font-size:24px}

  /* back */
  .section-title{position:absolute;font-family:"Montserrat",sans-serif;font-weight:700;color:var(--gold);line-height:1}
  .section-title--services{left:38px;top:34px;font-size:44px}
  .service-list{position:absolute;left:38px;top:100px;list-style:none;font-family:"Montserrat",sans-serif;font-weight:700;font-size:18px;line-height:1.1;color:var(--charcoal)}
  .service-list li{display:flex;gap:6px;margin-bottom:17px}
  .service-list svg{flex:none;margin-top:1px}
  .side-photo{position:absolute;left:292px;width:200px;height:136px;border-radius:10px}
  .side-photo--framing{top:72px;background:linear-gradient(180deg,#5f93d4 0%,#9bbbe0 35%,#c9a06a 55%,#a07a48 100%)}
  .side-photo--deck{top:222px;background:linear-gradient(180deg,#4f7a3c 0%,#7f8a76 35%,#d9a86a 65%,#c4894a 100%)}

  .process-kicker{position:absolute;left:38px;top:336px;font-family:"Montserrat",sans-serif;font-weight:600;font-size:28px;color:var(--charcoal);line-height:1}
  .section-title--process{left:36px;top:364px;font-size:50px}
  .steps{position:absolute;left:38px;top:418px;list-style:none}
  .steps li{display:flex;gap:10px;align-items:flex-start;height:62px;font-size:15px;line-height:1.2;color:var(--charcoal)}
  .steps__num{flex:none;width:34px;height:34px;margin-top:6px;background:var(--charcoal);color:var(--white);font-family:"Montserrat",sans-serif;font-weight:700;font-size:19px;display:flex;align-items:center;justify-content:center}

  .postcard--back .brand{left:565px;top:110px}
  .stamp-box{position:absolute;left:792px;top:28px;width:82px;height:82px;background:var(--stamp)}
  .address-line{position:absolute;left:553px;width:280px;height:1px;background:var(--rule)}

  .consult-panel{position:absolute;left:480px;top:447px;width:420px;height:153px;background:var(--charcoal);clip-path:polygon(52px 0,100% 0,100% 100%,0 100%,0 52px);color:var(--white);text-align:center;font-family:"Montserrat",sans-serif;padding:20px 0 0 20px;white-space:nowrap}
  .consult-panel__label{font-size:19px;font-weight:500}
  .consult-panel__phone{font-size:46px;font-weight:600;line-height:1.05;margin-top:4px}
  .consult-panel__web{font-size:21px;font-weight:700}
</style>
</head>
<body>

<section class="postcard postcard--front" aria-label="Postcard front">
  <div class="hero-photo" role="img" aria-label="Storm-damaged houses with stripped roofs under a blue sky"></div>
  <h1 class="headline">
    <span class="headline__top">POST STORM</span>
    <span class="headline__bottom">REPAIR SPECIAL</span>
  </h1>
  <div class="brand"><span class="brand__mark"></span>CREST ROOFING</div>

  <div class="offer">
    <div class="offer__headline">
      <span class="offer__amount">$200</span>
      <span class="offer__off">OFF</span>
    </div>
    <span class="offer__what">ANY REPAIR*</span>
    <span class="offer__terms">*some rules may apply</span>
  </div>
  <div class="thumb thumb--shingles" role="img" aria-label="Close-up of wind-torn roof shingles"></div>
  <div class="thumb thumb--tiles" role="img" aria-label="Roofer repairing clay tiles"></div>

  <div class="front-contact front-contact--phone">
    <svg width="38" height="38" viewBox="0 0 24 24" aria-hidden="true"><path fill="#e8b330" d="M6.6 10.8a15.1 15.1 0 0 0 6.6 6.6l2.2-2.2c.3-.3.7-.4 1-.2 1.1.4 2.3.6 3.6.6.6 0 1 .4 1 1V20c0 .6-.4 1-1 1A17 17 0 0 1 3 4c0-.6.4-1 1-1h3.5c.6 0 1 .4 1 1 0 1.3.2 2.5.6 3.6.1.3 0 .7-.2 1z"/></svg>
    877.512.DUNE
  </div>
  <div class="front-contact front-contact--web">
    <svg width="18" height="18" viewBox="0 0 24 24" aria-hidden="true"><circle cx="12" cy="12" r="10" fill="none" stroke="#e8b330" stroke-width="2.5"/><path d="M2 12h20M12 2c3 3 3 17 0 20M12 2c-3 3-3 17 0 20" fill="none" stroke="#e8b330" stroke-width="2"/></svg>
    www.DuneRoofingco.example
  </div>
</section>

<section class="postcard postcard--back" aria-label="Postcard back">
  <h2 class="section-title section-title--services">SERVICES</h2>
  <ul class="service-list">
    <li><svg width="17" height="17" viewBox="0 0 20 20" aria-hidden="true"><circle cx="10" cy="10" r="10" fill="#e8b330"/><path d="M5.5 10.5l3 3 6-6.5" fill="none" stroke="#fff" stroke-width="2.2"/></svg><span>RETAIL/COMMERCIAL<br>ROOF REPLACEMENT</span></li>
    <li><svg width="17" height="17" viewBox="0 0 20 20" aria-hidden="true"><circle cx="10" cy="10" r="10" fill="#e8b330"/><path d="M5.5 10.5l3 3 6-6.5" fill="none" stroke="#fff" stroke-width="2.2"/></svg><span>STORM DAMAGE ROOF<br>REPLACEMENT</span></li>
    <li><svg width="17" height="17" viewBox="0 0 20 20" aria-hidden="true"><circle cx="10" cy="10" r="10" fill="#e8b330"/><path d="M5.5 10.5l3 3 6-6.5" fill="none" stroke="#fff" stroke-width="2.2"/></svg><span>REPAIRS &amp;<br>RESTORATION</span></li>
    <li><svg width="17" height="17" viewBox="0 0 20 20" aria-hidden="true"><circle cx="10" cy="10" r="10" fill="#e8b330"/><path d="M5.5 10.5l3 3 6-6.5" fill="none" stroke="#fff" stroke-width="2.2"/></svg><span>NEW CONSTRUCTION</span></li>
  </ul>
  <div class="side-photo side-photo--framing" role="img" aria-label="New roof framing and decking under construction"></div>
  <div class="side-photo side-photo--deck" role="img" aria-label="Aerial view of crew installing roof decking"></div>

  <p class="process-kicker">CREST ROOFING</p>
  <h2 class="section-title section-title--process">PROCESS</h2>
  <ol class="steps">
    <li><span class="steps__num">01</span><span>Complimentary consultation to access your roofing<br>needs and review our honest recommendations.</span></li>
    <li><span class="steps__num">02</span><span>Our team of professionals replace, restore, or repair<br>your roof making the process as stress-free as possible.</span></li>
    <li><span class="steps__num">03</span><span>100% satisfaction, peace of mind, and continued<br>professional coverage backed by CREST Protection*.</span></li>
  </ol>

  <div class="brand"><span class="brand__mark"></span>CREST ROOFING</div>
  <div class="stamp-box" aria-label="Postage area"></div>
  <div class="address-line" style="top:265px"></div>
  <div class="address-line" style="top:325px"></div>
  <div class="address-line" style="top:385px"></div>

  <div class="consult-panel">
    <p class="consult-panel__label">Request Consultation</p>
    <p class="consult-panel__phone">877.512.DUNE</p>
    <p class="consult-panel__web">www.DuneRoofingco.example</p>
  </div>
</section>

</body>
</html>
```